Website redesign for Halt and Fullmane

We would like to update the design of our current website to a more concise, conversion optimized design.
The goal of our website is to get our message across as concisely as possible plus encourage people to contact us for more information or to book a consultation.
We need a redesign of the home page and 1 internal page - just for design/layout purposes/format purposes.

Target Market(s)

Males 20-45 years old who are concerned about hair loss and who want to regrow their own hair.

Industry/Entity Type

Health And Wellness

Number of Pages Required

2 page

Font styles to use
Sans Serif

Colors
00a990
33a6d7
ffffff
9d9d9d

Requirements
Must have
• We want the home page to be very concise and to the point in getting the message across. We want to get across the following 6 key messages:
• 1. Dr Pembrook story – why he created this solution
• 2. Hair loss is caused by a chemical imbalance
• 3. Halt and fullmane conducts genetic and DNA analysis, then rebalances body chemistry, thus reversing the hair loss process and enabling your own hair to regrow naturally
• 4. Money back guaranteed results
• 5. Purely Core ingredients – no harsh preservatives or chemicals are included
• 6. All ingredients are FDA approved and safe – no side effects
• We also need a strong call to action. We want people to call or email us to find out more information or to schedule a consultation.
• Here is our current website which is not performing as we would hope: http://www.haltandfullmane.example/
• Here is our press release for further information: https://www.pressdeskhub.example/news/finally-we-now-have-a-cure-for-male-pattern-baldness-28461902
• I uploaded the logo files, but let me know if anything else is needed and I can add it.

```html
<!DOCTYPE html>
<html lang="en">
<head>
<meta charset="utf-8">
<title>Halt and Fullmane – Home</title>
<link href="https://fonts.googleapis.com/css2?family=Mulish:wght@300;400;600;700&display=swap" rel="stylesheet">
<style>
:root{
  --teal:#00a990;
  --blue:#33a6d7;
  --blue-dark:#1f8fcf;
  --white:#ffffff;
  --grey:#9d9d9d;
  --grey-card:#9a9a9a;
  --text:#555a5e;
  --text-soft:#8a8f93;
  --panel:#eef0f1;
}
*{box-sizing:border-box;margin:0;padding:0}
html,body{width:1200px;height:2466px;overflow:hidden}
body{font-family:"Mulish",Arial,sans-serif;color:var(--text);background:var(--white);position:relative}
a{color:inherit;text-decoration:none}

/* header */
.site-header{position:absolute;top:0;left:0;width:1200px;height:108px;background:var(--white)}
.brand{position:absolute;left:118px;top:26px;display:flex;align-items:center;gap:14px}
.brand-mark{width:44px;height:44px;border-radius:50%;background:var(--teal)}
.brand-name{font-size:32px;font-weight:400;color:#4f6b73;line-height:1.1}
.brand-sub{font-size:19px;color:var(--blue);display:block;margin-top:2px}
.call{position:absolute;right:114px;top:34px;text-align:right}
.call-label{font-size:20px;color:var(--blue)}
.call-number{font-size:22px;color:#3a3f42;display:flex;align-items:center;gap:6px;justify-content:flex-end;margin-top:4px}

/* nav */
.main-nav{position:absolute;top:108px;left:0;width:1200px;height:53px;background:linear-gradient(#49b7e6,#2f9fd6)}
.main-nav ul{list-style:none;display:flex;position:absolute;left:128px;top:0;height:53px}
.main-nav li{font-size:17px;color:var(--white);padding:0 12px;line-height:53px;border-right:1px solid rgba(255,255,255,.35)}
.main-nav li:last-child{border-right:none}

/* hero */
.hero{position:absolute;top:161px;left:0;width:1200px;height:510px;background:linear-gradient(100deg,#19b6a5 0%,#1fbab1 40%,#3aaed9 100%)}
.hero-copy{position:absolute;left:118px;top:108px;color:var(--white)}
.hero-title{font-size:27px;font-weight:600;line-height:1.3}
.hero-guarantee{font-size:26px;font-weight:600;margin-top:14px}
.hero-text{font-size:18px;line-height:1.45;margin-top:18px}
.hero-cta{display:inline-block;margin-top:26px;border:2px solid var(--white);color:var(--white);font-size:19px;padding:10px 24px}
.hero-video{position:absolute;left:615px;top:83px;width:471px;height:312px;border:5px solid var(--white);background:linear-gradient(135deg,#c9d4d8,#a6b3b8 60%,#8d989c)}
.play{position:absolute;left:50%;top:50%;width:86px;height:86px;margin:-43px 0 0 -43px}
.slider-dots{position:absolute;left:548px;top:472px;display:flex;gap:9px}
.slider-dots span{width:14px;height:14px;border-radius:50%;background:var(--white)}
.slider-dots span.active{background:transparent;border:2px solid var(--white)}

/* intro */
.intro{position:absolute;top:671px;left:0;width:1200px;height:413px;text-align:center}
.intro h2{font-size:25px;font-weight:400;line-height:1.3;color:#4a4f53;margin-top:66px}
.intro p{width:850px;margin:30px auto 0;font-size:14px;line-height:2;color:var(--text-soft)}
.btn-learn{display:inline-block;margin-top:28px;background:var(--blue);color:var(--white);font-size:16px;padding:11px 35px}

/* why us */
.why{position:absolute;top:1084px;left:0;width:1200px;height:463px;background:var(--panel)}
.why-badge{position:absolute;left:567px;top:-33px;width:66px;height:66px;border-radius:50%;background:var(--white);display:flex;align-items:center;justify-content:center}
.why-badge span{width:34px;height:34px;border-radius:50%;background:var(--teal)}
.why h2{position:absolute;top:46px;width:100%;text-align:center;font-size:28px;font-weight:400;color:var(--teal)}
.why-item{position:absolute;display:flex;align-items:center;gap:18px;font-size:15px;line-height:1.5;color:#4f5458}
.why-icon{flex:none;width:74px;height:74px;border-radius:50%;border:2px solid var(--teal);display:flex;align-items:center;justify-content:center;background:var(--white)}

/* feature cards */
.features{position:absolute;top:1547px;left:0;width:1200px;height:519px}
.hair-deco{position:absolute;top:20px;width:130px;height:110px;background:linear-gradient(to bottom,rgba(0,0,0,0),rgba(0,0,0,.08))}
.card{position:absolute;top:130px;width:295px;height:290px;color:var(--white);text-align:center;padding:0 18px}
.card-teal{background:var(--teal)}
.card-blue{background:var(--blue)}
.card-grey{background:var(--grey-card)}
.card-icon{height:58px;margin-top:-18px;display:flex;align-items:center;justify-content:center;font-size:60px;font-weight:300;line-height:1}
.card h3{font-size:20px;font-weight:400;line-height:1.25;margin-top:14px}
.card p{font-size:12px;line-height:1.65;margin-top:12px}
.btn-read{position:absolute;bottom:-18px;left:50%;transform:translateX(-50%);width:132px;height:36px;border-radius:18px;border:2px solid var(--white);font-size:14px;line-height:32px;color:var(--white)}
.card-teal .btn-read{background:#0ab79c}
.card-blue .btn-read{background:var(--blue-dark)}
.card-grey .btn-read{background:#6f6f6f}

/* footer */
.site-footer{position:absolute;top:2066px;left:0;width:1200px;height:400px;background:var(--grey);color:var(--white)}
.footer-col{position:absolute;top:65px}
.footer-col h4{font-size:19px;font-weight:400;margin-bottom:10px}
.footer-col li{list-style:none;font-size:15px;line-height:28px}
.contact-line{display:flex;gap:10px}
.social{display:flex;gap:10px;margin-top:6px}
.social span{width:36px;height:36px;border-radius:50%;background:#b4b4b4}
.footer-rule{position:absolute;left:118px;top:312px;width:964px;height:1px;background:rgba(255,255,255,.3)}
.copyright{position:absolute;top:340px;width:100%;text-align:center;font-size:12px;color:#eeeeee}
</style>
</head>
<body>

<header class="site-header">
  <div class="brand">
    <span class="brand-mark"></span>
    <div class="brand-name">Halt &amp; Fullmane<span class="brand-sub">by Edwin Pembrook M.D.</span></div>
  </div>
  <div class="call">
    <div class="call-label">Call Us Now</div>
    <div class="call-number">
      <svg width="20" height="20" viewBox="0 0 24 24"><path fill="#33a6d7" d="M6.6 10.8c1.4 2.8 3.8 5.1 6.6 6.6l2.2-2.2c.3-.3.7-.4 1-.2 1.1.4 2.3.6 3.6.6.6 0 1 .4 1 1V20c0 .6-.4 1-1 1C10.6 21 3 13.4 3 4c0-.6.4-1 1-1h3.5c.6 0 1 .4 1 1 0 1.3.2 2.5.6 3.6.1.3 0 .7-.2 1z"/></svg>
      (555) 014-2290
    </div>
  </div>
</header>

<nav class="main-nav">
  <ul>
    <li>ABOUT US</li><li>HOW IT WORKS</li><li>SUCCESS STORIES</li><li>FAQS</li><li>BLOG</li><li>SALON PARTNERS</li><li>BOOK NOW</li><li>CONTACT</li>
  </ul>
</nav>

<section class="hero">
  <div class="hero-copy">
    <h1 class="hero-title">The First Non-Surgical Hair Loss<br>Solution With Clinically Proven Results</h1>
    <div class="hero-guarantee">100% Money Back Guarantee! *</div>
    <p class="hero-text">Stop Hereditary Hair Loss And Regrow a<br>Full, Healthy Head of Hair</p>
    <a class="hero-cta" href="#">Are You a Candidate?</a>
  </div>
  <div class="hero-video" role="img" aria-label="Video still of a man checking his hairline">
    <svg class="play" viewBox="0 0 86 86"><circle cx="43" cy="43" r="40" fill="none" stroke="#fff" stroke-width="5"/><path d="M35 27 L60 43 L35 59 Z" fill="#fff"/></svg>
  </div>
  <div class="slider-dots"><span class="active"></span><span></span><span></span><span></span></div>
</section>

<section class="intro">
  <h2>The Revolutionary New Solution For Hair Loss<br>That Uses Personalized Medicine To Stop Hair Loss and<br>Regrow Your Thinning / Receding Hair.</h2>
  <p>Dr. Edwin Pembrook, the creator of Halt and Fullmane is a renowned hair restoration expert. After seeing first his father and then older brothers thin and go bald, he dedicated his life to finding the cure for hair loss. After initially pioneering the single hair method for hair transplant, he determined there must be a non-surgical solution and spent the last 20 years in research and clinical trial and error first creating, then perfecting what is now the Halt and Fullmane solution for hair loss.</p>
  <a class="btn-learn" href="#">LEARN MORE</a>
</section>

<section class="why">
  <div class="why-badge"><span></span></div>
  <h2>WHY US</h2>

  <div class="why-item" style="left:180px;top:130px">
    <span class="why-icon"><svg width="40" height="40" viewBox="0 0 40 40" fill="none" stroke="#00a990" stroke-width="2.5"><path d="M10 6v10a8 8 0 0 0 16 0V6"/><path d="M18 24v6a6 6 0 0 0 12 0v-4"/><circle cx="30" cy="22" r="4"/></svg></span>
    <span>Dr Pembrook story – why he<br>created this solution</span>
  </div>
  <div class="why-item" style="left:672px;top:130px">
    <span class="why-icon"><svg width="40" height="40" viewBox="0 0 40 40"><circle cx="20" cy="20" r="13" fill="#00a990"/><text x="20" y="26" text-anchor="middle" font-size="17" font-family="Mulish,sans-serif" font-weight="700" fill="#fff">$</text></svg></span>
    <span>Money back<br>guaranteed results</span>
  </div>
  <div class="why-item" style="left:180px;top:230px">
    <span class="why-icon"><svg width="40" height="40" viewBox="0 0 40 40" fill="none" stroke="#00a990" stroke-width="2.5"><circle cx="20" cy="20" r="5"/><circle cx="8" cy="10" r="3"/><circle cx="32" cy="10" r="3"/><circle cx="8" cy="31" r="3"/><circle cx="32" cy="31" r="3"/><path d="M10 12l6 5M30 12l-6 5M10 29l6-5M30 29l-6-5"/></svg></span>
    <span>Hair loss is caused by a<br>chemical imbalance</span>
  </div>
  <div class="why-item" style="left:672px;top:230px">
    <span class="why-icon"><svg width="40" height="40" viewBox="0 0 40 40"><path d="M20 36V14" stroke="#00a990" stroke-width="2.5"/><ellipse cx="13" cy="16" rx="7" ry="4" fill="#00a990" transform="rotate(30 13 16)"/><ellipse cx="27" cy="16" rx="7" ry="4" fill="#00a990" transform="rotate(-30 27 16)"/><ellipse cx="20" cy="8" rx="4" ry="6" fill="#00a990"/></svg></span>
    <span>Purely Core ingredients – no harsh<br>preservatives or chemicals are included</span>
  </div>
  <div class="why-item" style="left:180px;top:325px">
    <span class="why-icon"><svg width="40" height="40" viewBox="0 0 40 40"><circle cx="20" cy="16" r="10" fill="#00a990"/><path d="M10 16v16h20V16z" fill="#00a990"/></svg></span>
    <span>Halt and fullmane conducts genetic and DNA<br>analysis, then rebalances body chemistry, thus<br>reversing the hair loss process and enabling<br>your own hair to regrow naturally</span>
  </div>
  <div class="why-item" style="left:672px;top:330px">
    <span class="why-icon"><svg width="40" height="40" viewBox="0 0 40 40" fill="none" stroke="#00a990" stroke-width="2.5"><path d="M15 6h10M17 6v10L8 32a2 2 0 0 0 2 3h20a2 2 0 0 0 2-3L23 16V6"/><path d="M12 26h16" /></svg></span>
    <span>All ingredients are FDA approved and<br>safe – no side effects</span>
  </div>
</section>

<section class="features">
  <div class="hair-deco" style="left:193px" role="img" aria-label="Decorative hair strands"></div>
  <div class="hair-deco" style="left:518px" role="img" aria-label="Decorative hair strands"></div>
  <div class="hair-deco" style="left:838px" role="img" aria-label="Decorative hair strands"></div>

  <article class="card card-teal" style="left:115px">
    <div class="card-icon">?</div>
    <h3>Why Is Halt and<br>Fullmane Unique?</h3>
    <p>Halt and Fullmane uses a scientific approach to hair loss by treating your unique cause. Every case is different and may include multiple causes. Unless we are treating yours, the treatment won't work for you.</p>
    <a class="btn-read" href="#">READ MORE</a>
  </article>
  <article class="card card-blue" style="left:435px">
    <div class="card-icon"><svg width="56" height="50" viewBox="0 0 56 50"><path d="M4 20h48a24 22 0 0 1-48 0z" fill="#fff"/><path d="M30 18L44 4" stroke="#fff" stroke-width="5" stroke-linecap="round"/></svg></div>
    <h3>Personalized<br>Medicine</h3>
    <p>Halt and Fullmane uses FDA approved ingredients in a proprietary formula using individual dosages based on your personal biology and genetics. Our solution is formulated in our specialty compounding</p>
    <a class="btn-read" href="#">READ MORE</a>
  </article>
  <article class="card card-grey" style="left:755px">
    <div class="card-icon"><svg width="56" height="56" viewBox="0 0 56 56" fill="none" stroke="#fff" stroke-width="2.5"><circle cx="28" cy="28" r="25"/><path d="M28 44c-10-6-10-20 0-30 10 10 10 24 0 30z"/><path d="M28 44V22"/></svg></div>
    <h3>Holistic<br>Approach</h3>
    <p>While many cases of hair loss are caused by a hormone imbalance (DHT), stress and diet can cause hair loss too. Your treatment will be multi-faceted to ensure your hair loss is stopped and we regrow your hair as quickly as possible.</p>
    <a class="btn-read" href="#">READ MORE</a>
  </article>
</section>

<footer class="site-footer">
  <div class="footer-col" style="left:137px">
    <h4>COMPANY</h4>
    <ul><li>About Us</li><li>How it Works</li><li>Success Stories</li><li>FAQ</li><li>Blog</li><li>Contact</li></ul>
  </div>
  <div class="footer-col" style="left:324px">
    <h4>HOURS OF OPERATION</h4>
    <ul><li>Monday - Friday: 9.00am to 5.00pm</li><li>Saturday: 8.00am to 2.00pm</li><li>Call Us (555) 014-2290</li><li>(555) 014-2290</li></ul>
  </div>
  <div class="footer-col" style="left:636px;top:62px">
    <h4>CONTACT US</h4>
    <ul>
      <li class="contact-line"><svg width="14" height="20" viewBox="0 0 14 20"><path d="M7 0a7 7 0 0 1 7 7c0 5-7 13-7 13S0 12 0 7a7 7 0 0 1 7-7z" fill="#fff"/><circle cx="7" cy="7" r="2.5" fill="#9d9d9d"/></svg><span>Halt and Fullmane Hair, LLC<br>1180 Larkspur Ave, Suite 200<br>Marlow Heights CA 90000</span></li>
      <li class="contact-line"><svg width="16" height="14" viewBox="0 0 16 14" style="margin-top:7px"><rect width="16" height="12" fill="#fff"/><path d="M0 0l8 6 8-6" stroke="#9d9d9d" fill="none"/></svg><span>Email Us</span></li>
      <li class="contact-line"><svg width="14" height="14" viewBox="0 0 24 24" style="margin-top:7px"><path fill="#fff" d="M6.6 10.8c1.4 2.8 3.8 5.1 6.6 6.6l2.2-2.2c.3-.3.7-.4 1-.2 1.1.4 2.3.6 3.6.6.6 0 1 .4 1 1V20c0 .6-.4 1-1 1C10.6 21 3 13.4 3 4c0-.6.4-1 1-1h3.5c.6 0 1 .4 1 1 0 1.3.2 2.5.6 3.6.1.3 0 .7-.2 1z"/></svg><span>(555) 014-2290</span></li>
    </ul>
  </div>
  <div class="footer-col" style="left:900px">
    <h4>FOLLOW US</h4>
    <div class="social"><span></span><span></span><span></span><span></span></div>
  </div>
  <div class="footer-rule"></div>
  <div class="copyright">© 2017 Company Name &nbsp;All right reserved &nbsp;Term of Use</div>
</footer>

</body>
</html>
```